Website Redesign project for agency

we're looking to see some new designs for an agency website.
details in this google doc: https://pages.quillmarsh.net/sheet/v/8QrtLm27vXcaPo91HsweKd4Zn0yBuTfg6521-qwLa3c/view?mode=shared
homepage and one inner page/ or the blog page
please visit the google doc above to see the website that needs to be redesigned as well as an example website we like.
if you have any questions please send them to us asap
thank you
Target Market(s)
small business owners
Number of Pages Required
2 page
Font styles to use
Sans Serif
Requirements
Nice to have
- custom design
Should not have
- do not use a template you find online

```html
<!DOCTYPE html>
<html lang="en">
<head>
<meta charset="utf-8">
<title>Rise &amp; Reach — Web Design Boston</title>
<link href="https://fonts.googleapis.com/css2?family=Montserrat:wght@500;600;700;800&family=Open+Sans:wght@400;600;700&display=swap" rel="stylesheet">
<style>
:root{
  --purple:#5a2ee0;
  --purple-dark:#3d17b8;
  --purple-deep:#2a0f8a;
  --green:#2fcf3f;
  --ink:#1d1d2b;
  --text:#55586a;
  --muted:#8c8fa0;
  --light:#f4f4f8;
  --line:#e4e4ee;
  --white:#ffffff;
}
*{margin:0;padding:0;box-sizing:border-box}
html,body{width:1200px;height:4840px;overflow:hidden}
body{position:relative;font-family:"Open Sans",Arial,sans-serif;color:var(--text);background:var(--white)}
h1,h2,h3,h4,.btn,.nav,.brand{font-family:"Montserrat",Arial,sans-serif}
section,header,footer{position:absolute;left:0;width:1200px}
.btn{display:inline-block;font-size:13px;font-weight:700;letter-spacing:.5px;padding:13px 26px;border-radius:30px;text-transform:uppercase;background:var(--green);color:var(--white)}
.btn.ghost{background:transparent;border:2px solid var(--white);padding:11px 24px}
.ph{position:absolute}
.sec-title{text-align:center;font-size:34px;font-weight:700;color:var(--ink);letter-spacing:1px}

/* hero */
.hero{top:0;height:470px;background:linear-gradient(100deg,var(--purple-deep) 0%,var(--purple) 55%,#7b54ee 100%);overflow:hidden}
.hero .photo{right:0;top:0;width:640px;height:470px;background:linear-gradient(90deg,rgba(90,46,224,0) 0%,rgba(190,160,140,.55) 45%,rgba(220,200,190,.6) 100%)}
.nav{position:absolute;top:0;left:0;width:1200px;height:60px;display:flex;align-items:center;padding:0 40px}
.brand{font-size:20px;font-weight:800;color:var(--white);display:flex;align-items:center;gap:8px}
.brand i{width:14px;height:14px;border-radius:50%;background:var(--green);display:block}
.menu{margin-left:auto;display:flex;gap:26px;align-items:center;font-size:12px;font-weight:600;color:var(--white);letter-spacing:.5px}
.menu .portal{border:2px solid var(--white);border-radius:20px;padding:8px 18px}
.hero-copy{position:absolute;left:40px;top:130px;width:330px;color:var(--white)}
.hero-copy .kick{font-family:Montserrat,sans-serif;color:var(--green);font-weight:800;font-size:30px;letter-spacing:1px}
.hero-copy h1{font-size:64px;font-weight:800;line-height:1;margin-bottom:16px}
.hero-copy p{font-size:14px;line-height:1.6;margin-bottom:24px}
.hero-copy .btn{margin-right:10px}
.hero svg{position:absolute;left:0;bottom:0}

/* services */
.services{top:470px;height:690px}
.services .sec-title{margin-top:80px}
.services .sub{text-align:center;font-size:14px;margin-top:18px}
.cards{display:flex;justify-content:center;gap:28px;margin-top:40px}
.card{width:260px;height:300px;background:var(--white);border-radius:10px;box-shadow:0 10px 30px rgba(40,30,100,.12);text-align:center;padding:36px 26px;position:relative}
.card .ico{width:72px;height:72px;margin:0 auto 22px;border-radius:50%;background:#efeaff;display:flex;align-items:center;justify-content:center}
.card h3{font-size:17px;color:var(--ink);margin-bottom:10px}
.card p{font-size:13px;line-height:1.5}
.card .plus{position:absolute;left:50%;bottom:-16px;margin-left:-16px;width:32px;height:32px;border-radius:50%;background:var(--white);border:2px solid var(--green);color:var(--green);font-weight:700;line-height:28px}
.services .cta{text-align:center;margin-top:64px}

/* about */
.about{top:1160px;height:600px}
.about .rings{left:70px;top:30px}
.about .portrait{left:130px;top:90px;width:380px;height:380px;border-radius:50%;background:radial-gradient(circle at 50% 40%,#e9ddd3,#b99a86)}
.about-copy{position:absolute;left:590px;top:40px;width:540px}
.about-copy h2{font-size:36px;color:var(--ink);font-weight:700;margin-bottom:18px}
.about-copy p{font-size:13px;line-height:1.75;margin-bottom:14px}

/* found */
.found{top:1760px;height:440px;background:var(--light);overflow:hidden}
.found svg.band{position:absolute;right:0;top:0}
.found-copy{position:absolute;left:40px;top:70px;width:340px}
.found-copy h2{font-size:40px;font-weight:800;line-height:1.1;color:var(--ink);margin-bottom:22px}
.found-copy h2 span{color:var(--purple)}
.found-copy p{font-size:14px;line-height:1.7;margin-bottom:24px}
.found .devices{left:440px;top:50px;width:560px;height:330px;border-radius:12px;background:linear-gradient(135deg,#2c2c3a,#8d8aa8 55%,#d9d6e6)}

/* projects */
.projects{top:2200px;height:1030px}
.projects .sec-title{margin-top:90px;font-size:32px}
.filters{display:flex;justify-content:center;align-items:center;gap:26px;margin-top:40px;font-family:Montserrat,sans-serif;font-size:13px;font-weight:700;color:var(--ink)}
.filters .arrow{width:34px;height:34px;border-radius:50%;border:1px solid var(--line);display:flex;align-items:center;justify-content:center;color:var(--muted)}
.filters .on{background:var(--green);color:var(--white);padding:9px 22px;border-radius:20px}
.grid{display:grid;grid-template-columns:repeat(3,340px);gap:36px 30px;justify-content:center;margin-top:36px}
.proj{background:var(--white);box-shadow:0 8px 24px rgba(40,30,100,.1);height:270px}
.proj .shot{position:relative;height:210px}
.proj h4{text-align:center;font-size:14px;color:var(--ink);padding-top:20px}
.projects .cta{text-align:center;margin-top:40px}

/* get started */
.start{top:3230px;height:330px;background:var(--light)}
.start .photo{left:0;top:0;width:600px;height:330px;background:linear-gradient(120deg,#33384a,#8a8f9c 55%,#d8dbe0)}
.start-copy{position:absolute;left:680px;top:70px;width:460px}
.start-copy h2{font-size:44px;font-weight:800;color:var(--ink);line-height:1.05}
.start-copy h2 span{color:var(--purple)}
.start-copy p{font-family:Montserrat,sans-serif;font-weight:600;font-size:16px;color:var(--ink);margin:14px 0 20px;line-height:1.4}

/* clients */
.clients{top:3580px;height:800px}
.clients .sec-title{margin-top:40px;font-size:32px}
.clients .sub{text-align:center;font-size:13px;line-height:1.6;width:760px;margin:20px auto 0}
.logos{display:flex;justify-content:space-between;width:1080px;margin:30px auto 0}
.logos .mark{width:140px;height:50px;background:#d9dae3;border-radius:4px}
.reviews{display:flex;justify-content:center;gap:40px;margin-top:56px}
.review{width:320px;height:400px;border:1px solid var(--line);border-radius:8px;position:relative;text-align:center;padding:50px 30px 0}
.review .q{position:absolute;left:50%;top:-16px;margin-left:-16px;width:32px;height:32px;border-radius:50%;background:var(--purple);color:var(--white);font-family:Montserrat,sans-serif;font-weight:800;line-height:34px}
.review p{font-size:13px;line-height:1.7;min-height:170px}
.review h4{font-size:15px;color:var(--ink);margin-top:20px}
.review small{display:block;font-size:12px;margin-top:4px;color:var(--muted)}
.review .avatar{width:64px;height:64px;border-radius:50%;margin:20px auto 0;background:linear-gradient(135deg,#cbb8a8,#8e7668)}

/* footer */
.footer{top:4400px;height:400px;background:linear-gradient(100deg,var(--purple-deep),var(--purple))}
.cols{display:flex;gap:50px;padding:60px 40px 0;color:#e4dcff}
.col h4{font-size:14px;color:var(--white);margin-bottom:16px;letter-spacing:.5px}
.col p,.col li{font-size:13px;line-height:1.8;list-style:none}
.col .lbl{font-family:Montserrat,sans-serif;font-weight:700;color:var(--white);font-size:12px;margin-top:6px}
.social{display:flex;gap:8px;margin-top:16px}
.social i{width:30px;height:30px;border-radius:50%;background:var(--green);display:block}
.col .btn{display:block;text-align:center;width:170px;margin-top:16px}
.copy{position:absolute;top:4800px;left:0;width:1200px;height:40px;background:var(--purple-deep);color:#c9bdfa;font-size:12px;text-align:center;line-height:40px}
</style>
</head>
<body>

<header class="hero">
  <div class="ph photo" role="img" aria-label="Photo of a smiling couple looking at a tablet together"></div>
  <nav class="nav">
    <div class="brand"><i></i>RISE &amp; REACH</div>
    <div class="menu"><span>WHAT WE DO ▾</span><span>PROJECTS</span><span>WHO WE ARE ▾</span><span>BOOK US</span><span class="portal">CLIENT PORTAL</span></div>
  </nav>
  <div class="hero-copy">
    <div class="kick">WEB DESIGN</div>
    <h1>BOSTON</h1>
    <p>A professionally designed website by Rise &amp; Reach makes your website attractive, functional and mobile friendly.</p>
    <span class="btn">Request Pricing</span><span class="btn ghost">Our Work</span>
  </div>
  <svg width="1200" height="120" viewBox="0 0 1200 120" aria-hidden="true">
    <path d="M560 120 C800 60 1000 20 1200 0 L1200 120 Z" fill="#2fcf3f"/>
    <path d="M0 120 L0 90 C300 120 700 110 1200 40 L1200 120 Z" fill="#ffffff"/>
  </svg>
</header>

<section class="services">
  <h2 class="sec-title">OUR SERVICES</h2>
  <p class="sub">Web Design, Search Engine Optimization or Social Media Marketing?</p>
  <div class="cards">
    <div class="card">
      <div class="ico"><svg width="36" height="36" viewBox="0 0 36 36"><rect x="4" y="7" width="28" height="19" rx="2" fill="none" stroke="#5a2ee0" stroke-width="2.5"/><path d="M13 31h10M18 26v5" stroke="#5a2ee0" stroke-width="2.5"/></svg></div>
      <h3>WEB DESIGN</h3><p>Web Design to convert site visitors into customers.</p><div class="plus">+</div>
    </div>
    <div class="card">
      <div class="ico"><svg width="36" height="36" viewBox="0 0 36 36"><circle cx="15" cy="15" r="9" fill="none" stroke="#5a2ee0" stroke-width="2.5"/><path d="M22 22l9 9" stroke="#5a2ee0" stroke-width="3"/></svg></div>
      <h3>SEO</h3><p>Search engine optimization for more traffic.</p><div class="plus">+</div>
    </div>
    <div class="card">
      <div class="ico"><svg width="36" height="36" viewBox="0 0 36 36"><path d="M5 8h26v16H14l-7 6v-6H5z" fill="none" stroke="#5a2ee0" stroke-width="2.5" stroke-linejoin="round"/></svg></div>
      <h3>SOCIAL MEDIA</h3><p>Engage in conversations with customers online.</p><div class="plus">+</div>
    </div>
  </div>
  <div class="cta"><span class="btn">I Want It All</span></div>
</section>

<section class="about">
  <svg class="ph rings" width="500" height="500" viewBox="0 0 500 500" aria-hidden="true">
    <circle cx="250" cy="250" r="245" fill="none" stroke="#ecebf3" stroke-width="2"/>
    <circle cx="250" cy="250" r="215" fill="none" stroke="#ecebf3" stroke-width="2"/>
  </svg>
  <div class="ph portrait" role="img" aria-label="Photo of a smiling woman holding a tablet"></div>
  <div class="about-copy">
    <h2>ABOUT RISE &amp; REACH</h2>
    <p>Whether you need a new Website, SEO, Social Media or marketing plan, we're up for the task. Rise &amp; Reach has a team of talented developers, designers and inbound marketers at your disposal. We'll help you own your local or national market within your industry.</p>
    <p>We're the most reviewed and highest rated Web Design company in Boston that focuses on services that include inbound marketing, search engine optimization, social media marketing, lead conversion, re-marketing, and marketing automation. We perform high-end mobile friendly web design, content creation, SEO, social media strategy development, email marketing and more. Our clients in Boston and around the country enjoy more website visitors, more conversions, and best of all a better return on investment.</p>
    <span class="btn" style="margin-top:8px">Request A Free Quote</span>
  </div>
</section>

<section class="found">
  <svg class="band" width="820" height="440" viewBox="0 0 820 440" aria-hidden="true">
    <path d="M200 0 H820 V440 H40 C260 360 180 120 200 0 Z" fill="#5a2ee0"/>
  </svg>
  <div class="found-copy">
    <h2>YOU FOUND THE TOP BOSTON <span>WEB DESIGN AGENCY!</span></h2>
    <p>All our custom websites are built with responsive design so they will look great on desktops, tablets, and mobile phones. Your customers will have no problem reaching you no matter which device they're on.</p>
    <span class="btn">Get Started</span>
  </div>
  <div class="ph devices" role="img" aria-label="Website shown on a laptop, tablet and phone"></div>
</section>

<section class="projects">
  <h2 class="sec-title">WEB DESIGN BOSTON PROJECTS</h2>
  <div class="filters">
    <span class="arrow">‹</span><span class="on">ALL</span><span>CONSTRUCTION</span><span>FITNESS</span><span>LANDSCAPING</span><span>NON-PROFIT</span><span>ROOFING</span><span class="arrow">›</span>
  </div>
  <div class="grid">
    <div class="proj"><div class="shot" role="img" aria-label="Construction website screenshot" style="background:linear-gradient(160deg,#7a8da6,#c9d3dd)"></div><h4>Construction Website Design</h4></div>
    <div class="proj"><div class="shot" role="img" aria-label="Roofing company website screenshot" style="background:linear-gradient(160deg,#5d6e52,#b6c2c9)"></div><h4>Roofing Company Web Design</h4></div>
    <div class="proj"><div class="shot" role="img" aria-label="Kitchen website screenshot" style="background:linear-gradient(160deg,#b23a3a,#e8e2dc)"></div><h4>Kitchen Website Design</h4></div>
    <div class="proj"><div class="shot" role="img" aria-label="Music website screenshot" style="background:linear-gradient(160deg,#e6c233,#3a4fb0)"></div><h4>Music Website Design</h4></div>
    <div class="proj"><div class="shot" role="img" aria-label="Recruiter website screenshot" style="background:linear-gradient(160deg,#9c9c9c,#e5e5e5)"></div><h4>Recruiter Website Design</h4></div>
    <div class="proj"><div class="shot" role="img" aria-label="Medical billing website screenshot" style="background:linear-gradient(160deg,#c8333a,#f1e6e6)"></div><h4>Medical Billing Website Design</h4></div>
  </div>
  <div class="cta"><span class="btn">Older Entries</span></div>
</section>

<section class="start">
  <div class="ph photo" role="img" aria-label="Photo of two business people meeting at a desk"></div>
  <div class="start-copy">
    <h2>LET'S<br><span>GET STARTED</span></h2>
    <p>Ready To Make A Real Change? Let's Build<br>This Thing Together!</p>
    <span class="btn">Tell Us About Your Project</span>
  </div>
</section>

<section class="clients">
  <h2 class="sec-title">HAPPY CLIENTS SAY</h2>
  <p class="sub">We do a lot more than just build awesome websites. We partner with all our clients to build relationships and create marketing plans that help them improve their business. But don't just take our word for it. See what our clients have to say.</p>
  <div class="logos"><div class="mark"></div><div class="mark"></div><div class="mark"></div></div>
  <div class="reviews">
    <div class="review"><div class="q">“</div>
      <p>Rise &amp; Reach was incredibly responsive, resourceful, and diligent. They built a beautiful site that exceeded our expectations. We would recommend them to anyone looking to grow their business with a website.</p>
      <h4>Mark Ellison</h4><small>Managing Member, Harbor Crest Partners</small><div class="avatar" role="img" aria-label="Client portrait"></div></div>
    <div class="review"><div class="q">“</div>
      <p>The team at Rise &amp; Reach has been terrific to work with. They provided valuable direction and insight. If you are looking for creative talent and strategic direction, they are the best choice.</p>
      <h4>Daniel Hart</h4><small>Founder &amp; CEO, Medical Billing Group</small><div class="avatar" role="img" aria-label="Client portrait"></div></div>
    <div class="review"><div class="q">“</div>
      <p>Rise &amp; Reach just redesigned our nonprofit website and we couldn't be happier with the results. The team is very pleasing to work with, professional, and responsive to our requests. I would definitely recommend them.</p>
      <h4>Lena Morales</h4><small>Secretary &amp; Chief Operational Officer</small><div class="avatar" role="img" aria-label="Client portrait"></div></div>
  </div>
</section>

<footer class="footer">
  <div class="cols">
    <div class="col" style="width:300px"><h4>READY TO GET STARTED?</h4><p>Ready to start a new project or curious about our process? Drop us a note or give us a call. We are happy to answer any questions and provide a free consultation.</p><div class="social"><i></i><i></i><i></i><i></i></div></div>
    <div class="col" style="width:180px"><h4>QUICK LINKS</h4><ul><li>› What We Do</li><li>› Projects</li><li>› Who We Are</li><li>› Book Us</li><li>› Client Portal</li><li>› Contact</li></ul></div>
    <div class="col" style="width:280px"><h4>CONTACT DETAILS</h4><p class="lbl">BOSTON WEBSITE DESIGN</p><p>214 Harbor Lane, Boston, MA 02110</p><p class="lbl">PHONE</p><p>617-555-0142</p><p class="lbl">EMAIL</p><p>hello@riseandreach.co</p></div>
    <div class="col" style="width:220px"><h4>OPERATING HOURS</h4><p>● Mon-Sat, 8AM – 8PM</p><span class="btn">Get In Touch</span><span class="btn ghost">Our Work</span></div>
  </div>
</footer>
<div class="copy">Copyright © 2024 Rise &amp; Reach. All Rights Reserved.</div>

</body>
</html>
```